New Business Card Design Project

We require a business card design for Vexalund, a newly established Indian company.
Our focus is on the development, manufacturing, and export of a diverse array of pharmaceutical products on a global scale. The card should convey a professional appearance, as our primary markets are in Africa, China, and Southeast Asian nations.
We envision a two-sided business card, with the reverse side dedicated to a logo set against a solid color or an elegantly designed pattern. The corners should be rounded. We would appreciate seeing both horizontal and vertical design options. We trust the designer to utilize their expertise in creating this design.

The content for the business card is included in the attached Word file.

Target Market(s)

Our primary markets are in Africa, China, and Southeast Asian, Latin America, Maldives, Sri Lanka

Industry/Entity Type

Pharmaceutical Manufacturing and Export

Contact Information for Business Card

Colors

Designer to choose colors to be used in the design.

Requirements
Must have
• The reverse side of the business card features solely the logo along with the tagline, "Remedies of Life."
Should not have
• The logo should not exceed two instances, encompassing both the front and back sides of the card.

```html
<!DOCTYPE html>
<html lang="en">
<head>
<meta charset="utf-8">
<title>Vexalund Business Card</title>
<link href="https://fonts.googleapis.com/css2?family=Lato:wght@400;700&family=Montserrat:wght@600;700&display=swap" rel="stylesheet">
<style>
  :root {
    --stage: #4e545c;
    --brand-blue: #29a9e1;
    --accent-red: #ef6150;
    --paper: #ffffff;
    --ink: #1c1c1c;
  }
  html, body {
    margin: 0;
    padding: 0;
    width: 1200px;
    height: 1120px;
    overflow: hidden;
    background: var(--stage);
  }
  .canvas {
    position: relative;
    width: 1200px;
    height: 1120px;
    background: var(--stage);
  }
  .card {
    position: absolute;
    border-radius: 27px;
    overflow: hidden;
  }
  /* Reverse side */
  .card-reverse {
    left: 156px;
    top: 120px;
    width: 726px;
    height: 414px;
    background: var(--brand-blue);
  }
  .reverse-mark {
    position: absolute;
    left: 311px;
    top: 85px;
    width: 110px;
    height: 110px;
    border-radius: 50%;
    background: var(--paper);
  }
  .reverse-name {
    position: absolute;
    left: 0;
    width: 726px;
    top: 242px;
    text-align: center;
    font-family: "Montserrat", sans-serif;
    font-weight: 700;
    font-size: 80px;
    line-height: 1;
    color: var(--paper);
    letter-spacing: -1px;
  }
  .tagline {
    position: absolute;
    left: -46px;
    width: 726px;
    top: 361px;
    text-align: center;
    font-family: "Montserrat", sans-serif;
    font-weight: 700;
    font-size: 28px;
    line-height: 1;
    color: var(--paper);
  }
  /* Front side */
  .card-front {
    left: 323px;
    top: 607px;
    width: 700px;
    height: 400px;
    background: var(--paper);
  }
  .front-mark {
    position: absolute;
    left: 508px;
    top: 64px;
    width: 64px;
    height: 64px;
    border-radius: 50%;
    background: var(--brand-blue);
  }
  .front-name {
    position: absolute;
    right: 48px;
    top: 168px;
    font-family: "Montserrat", sans-serif;
    font-weight: 700;
    font-size: 49px;
    line-height: 1;
    color: var(--brand-blue);
    letter-spacing: -0.5px;
  }
  .person {
    position: absolute;
    left: 45px;
    top: 229px;
    font-family: "Lato", sans-serif;
  }
  .person-name {
    margin: 0;
    font-weight: 700;
    font-size: 29px;
    line-height: 34px;
    color: var(--brand-blue);
    letter-spacing: -0.5px;
  }
  .person-role {
    margin: 0;
    font-weight: 400;
    font-size: 19.5px;
    line-height: 24px;
    color: var(--ink);
  }
  .divider {
    position: absolute;
    left: 47px;
    top: 296px;
    width: 611px;
    height: 1.5px;
    background: var(--ink);
  }
  .contacts {
    position: absolute;
    left: 45px;
    top: 316px;
    margin: 0;
    padding: 0;
    list-style: none;
    font-family: "Lato", sans-serif;
    font-size: 16.5px;
    color: var(--ink);
  }
  .contacts li {
    display: flex;
    align-items: center;
    height: 20px;
  }
  .contacts svg {
    width: 14px;
    height: 14px;
    margin-right: 9px;
    flex: none;
  }
  .address {
    position: absolute;
    right: 42px;
    top: 328px;
    margin: 0;
    text-align: right;
    font-family: "Lato", sans-serif;
    font-style: normal;
    font-size: 16.5px;
    line-height: 20px;
    color: var(--ink);
  }
</style>
</head>
<body>
<main class="canvas">

  <section class="card card-reverse" aria-label="Card reverse side">
    <div class="reverse-mark" aria-hidden="true"></div>
    <div class="reverse-name">Vexalund</div>
    <div class="tagline">Remedies of Life</div>
  </section>

  <section class="card card-front" aria-label="Card front side">
    <div class="front-mark" aria-hidden="true"></div>
    <div class="front-name">Vexalund</div>

    <div class="person">
      <p class="person-name">ANDREW COLLINS</p>
      <p class="person-role">MANAGING DIRECTOR</p>
    </div>

    <div class="divider"></div>

    <ul class="contacts">
      <li>
        <svg viewBox="0 0 16 16" aria-hidden="true"><path fill="var(--accent-red)" d="M3.6 1.2l2.3 2.6-1.3 1.6c.9 2 2.6 3.7 4.9 4.9l1.6-1.3 2.6 2.3-1.4 2.4C7.3 13.6 2.4 8.7 1.3 3.7z"/><path d="M9.5 2.5a4 4 0 014 4M9.3 4.6a2 2 0 012.1 2.1" stroke="var(--accent-red)" stroke-width="1.3" fill="none"/></svg>
        <span>044-987 650 321</span>
      </li>
      <li>
        <svg viewBox="0 0 16 16" aria-hidden="true"><rect x="1" y="3.5" width="14" height="10" fill="var(--accent-red)"/><path d="M1.5 4l6.5 5 6.5-5" stroke="#fff" stroke-width="1.2" fill="none"/></svg>
        <span>info@vexalund.com</span>
      </li>
      <li>
        <svg viewBox="0 0 16 16" aria-hidden="true"><circle cx="8" cy="8" r="7" fill="var(--accent-red)"/><path d="M5 3.5c1.5 1 1 2.5 2.5 3s1 2 0 3.5M10.5 9.5c1 .3 1.8 1.5 1.5 3" stroke="#fff" stroke-width="1.3" fill="none"/></svg>
        <span>www.vexalund.com</span>
      </li>
    </ul>

    <address class="address">421, Address line goes here<br>45452, Country name</address>
  </section>

</main>
</body>
</html>
```